Verodex business card

Business card for sustainable investment company called "Verodex". Verodex is an exchange platform selling carbon credits between buyers and sellers. Carbon Credits are an environmental commodity for reducing global carbon emissions.

the card should obviously have our logo and the theme should be sustainability/environment mixed with a trading platform.

Contact Information for Business Card

Logo, Name, Title, Phone, Email

Colors
0054AA
0677BA
7BADD7
CADEEF
E8F1F8
0094D4
00A9DD
6FCCEA
C7EBF8
E9F6FB
00AB8E
00BBA5
67D7C9
C6EFE9
E9F9F6
59FF00
82FF00
B8FF75
E3FFCB
F4FFEA

```html
<!DOCTYPE html>
<html lang="en">
<head>
<meta charset="utf-8">
<title>Verodex business card</title>
<link rel="stylesheet" href="https://fonts.googleapis.com/css2?family=Raleway:wght@400;500;700&display=swap">
<style>
  :root {
    --backdrop: #8e8e8e;
    --paper: #ffffff;
    --navy: #0c2951;
    --navy-band: #1f3452;
    --aqua: #36e6ec;
    --blue: #1e6ce8;
    --brand-blue: #1f86ea;
    --ink-light: #ffffff;
  }
  html, body {
    margin: 0;
    width: 1200px;
    height: 1200px;
    overflow: hidden;
    background: var(--backdrop);
    font-family: "Raleway", sans-serif;
  }
  .card-slot {
    position: absolute;
    left: 281px;
    width: 642px;
    height: 366px;
  }
  .card-slot.front-slot { top: 195px; }
  .card-slot.back-slot { top: 639px; }
  .card {
    position: absolute;
    left: 0; top: 0;
    width: 802px;
    height: 457px;
    border-radius: 24px;
    overflow: hidden;
    transform: scale(0.8);
    transform-origin: top left;
  }
  .card-front { background: var(--paper); }
  .card-back { background: var(--navy); }
  .wave-art {
    position: absolute;
    inset: 0;
    width: 802px;
    height: 457px;
  }
  .brand {
    position: absolute;
    display: flex;
    align-items: center;
    gap: 18px;
    font-weight: 700;
    letter-spacing: 1px;
  }
  .brand-dot {
    border-radius: 50%;
    background: var(--brand-blue);
    flex: none;
  }
  .front-brand {
    left: 82px;
    top: 150px;
    color: var(--brand-blue);
    font-size: 46px;
  }
  .front-brand .brand-dot { width: 52px; height: 52px; }
  .back-brand {
    left: 0; right: 0;
    top: 180px;
    justify-content: center;
    color: var(--ink-light);
    font-size: 76px;
  }
  .back-brand .brand-dot { width: 96px; height: 96px; }
  .holder {
    position: absolute;
    right: 52px;
    top: 254px;
    text-align: right;
    color: var(--ink-light);
  }
  .holder-name {
    margin: 0;
    font-size: 37px;
    font-weight: 700;
    line-height: 1.1;
    white-space: nowrap;
  }
  .holder-title {
    margin: 2px 0 0;
    font-size: 21px;
    font-weight: 400;
  }
  .contact-list {
    list-style: none;
    margin: 18px 0 0;
    padding: 0;
    font-size: 19px;
    font-weight: 400;
  }
  .contact-list li {
    display: flex;
    justify-content: flex-end;
    align-items: center;
    gap: 14px;
    height: 28.5px;
    white-space: nowrap;
  }
  .contact-icon { width: 18px; height: 18px; flex: none; }
</style>
</head>
<body>
  <div class="card-slot front-slot">
    <section class="card card-front" aria-label="Business card front">
      <svg class="wave-art" viewBox="0 0 802 457" aria-hidden="true">
        <defs>
          <linearGradient id="sea-gradient" x1="0" y1="0" x2="1" y2="0">
            <stop offset="0" stop-color="var(--aqua)"/>
            <stop offset="1" stop-color="var(--blue)"/>
          </linearGradient>
        </defs>
        <path fill="var(--navy-band)" d="M0,358 C150,400 270,370 350,282 C430,200 560,95 802,86 L802,124 C600,122 480,180 390,262 C300,345 190,405 0,402 Z"/>
        <path fill="url(#sea-gradient)" d="M0,412 C200,430 300,380 380,300 C460,220 540,150 802,150 L802,457 L0,457 Z"/>
      </svg>
      <div class="brand front-brand"><span class="brand-dot"></span>VERODEX</div>
      <div class="holder">
        <h1 class="holder-name">MARCUS HALE</h1>
        <p class="holder-title">Founder &amp; CEO</p>
        <ul class="contact-list">
          <li>(555) 014-2087
            <svg class="contact-icon" viewBox="0 0 24 24" aria-hidden="true"><path fill="#fff" d="M6.6 10.8a15 15 0 0 0 6.6 6.6l2.2-2.2a1 1 0 0 1 1-.25 11.4 11.4 0 0 0 3.6.57 1 1 0 0 1 1 1V20a1 1 0 0 1-1 1A17 17 0 0 1 3 4a1 1 0 0 1 1-1h3.5a1 1 0 0 1 1 1c0 1.250.2 2.450.57 3.57a1 1 0 0 1-.25 1z"/></svg>
          </li>
          <li>office@verodex.com
            <svg class="contact-icon" viewBox="0 0 24 24" aria-hidden="true"><rect x="2" y="5" width="20" height="14" rx="1.5" fill="#fff"/><path d="M3 6.5l9 6.5 9-6.5" fill="none" stroke="#2a7ae8" stroke-width="1.8"/></svg>
          </li>
          <li>verodex.com
            <svg class="contact-icon" viewBox="0 0 24 24" aria-hidden="true"><circle cx="12" cy="12" r="9" fill="none" stroke="#fff" stroke-width="2"/><path fill="#fff" d="M8 6c2 1 3 3 2 5s-3 1-3 3 2 3 1 5c-2-1-4-4-4-7 0-2 1-4 4-6zm7 1c2 1 3 2 3 4-2 0-3 1-3 3s1 3 0 5c-1-1-2-3-1-5s-1-3 0-5 1-1 1-2z"/></svg>
          </li>
        </ul>
      </div>
    </section>
  </div>

  <div class="card-slot back-slot">
    <section class="card card-back" aria-label="Business card back">
      <div class="brand back-brand"><span class="brand-dot"></span>VERODEX</div>
    </section>
  </div>
</body>
</html>
```